Website for a new t-shirt company called bolddawnapperal.com

We are looking for a talented web designer to create a website that aligns with our brand's message and identity centered around the theme of "Bold Dawn." The website should be modern, clean, and visually appealing while also being user-friendly and easy to navigate.

We will be using the Big Commerce platform for our online store section, so the designer should have experience in designing websites on this platform.

We would like the website to have the following elements:

A color scheme that aligns with the brand's identity and message
A homepage that showcases our products and message, with clear calls-to-action for visitors to explore further
A blog section that highlights our brand's philosophy and offers advice and tips for people looking to make positive changes in their lives
An "About Us" section that introduces our brand and team and offers insight into our mission and values
A contact form that allows visitors to easily get in touch with us for inquiries or support
We are open to creative suggestions and ideas from the designer, but we would like the website to have a modern and minimalist aesthetic that resonates with our target audience of 20 to 40-year-olds.

```html
<!DOCTYPE html>
<html lang="en">
<head>
<meta charset="utf-8">
<title>Bold Dawn — T-Shirts</title>
<link href="https://fonts.googleapis.com/css2?family=Kaushan+Script&family=Poppins:wght@400;500;600;700&display=swap" rel="stylesheet">
<style>
:root{
  --ink:#000;
  --white:#fff;
  --paper:#f1f1f1;
  --strip:#e4e4e4;
  --muted:#444;
  --line:#d9d9d9;
  --star:#e7b400;
  --accent:#1e6fd9;
}
*{box-sizing:border-box;margin:0;padding:0}
html,body{width:1200px;height:5000px;overflow:hidden}
body{font-family:'Poppins',sans-serif;color:var(--ink);background:var(--white);position:relative}
.script{font-family:'Kaushan Script',cursive}
.abs{position:absolute}
.btn{display:inline-block;background:var(--ink);color:var(--white);font-family:'Kaushan Script',cursive;font-size:15px;padding:6px 22px;letter-spacing:.5px}

/* header */
.site-header{position:absolute;top:0;left:0;width:1200px;height:82px;display:flex;align-items:center;padding:0 90px}
.logo{font-size:30px;font-weight:600;width:260px}
.main-nav{display:flex;gap:26px;font-weight:600;font-size:17px}
.header-icons{margin-left:auto;display:flex;gap:16px}
.search-bar{position:absolute;top:82px;left:0;width:1200px;height:83px;background:var(--ink);display:flex;align-items:center;padding:0 92px}
.search-field{width:760px;height:48px;background:var(--white);display:flex;align-items:center;justify-content:space-between;padding:0 6px 0 16px;font-size:15px}
.search-btn{width:36px;height:36px;background:var(--ink);display:flex;align-items:center;justify-content:center}
.perk{display:flex;align-items:center;gap:10px;color:var(--white);font-size:16px;line-height:1.15;margin-left:34px}
.promo{position:absolute;top:165px;left:0;width:1200px;height:30px;background:var(--strip);text-align:center;font-size:14px;line-height:30px}

/* hero */
.hero{position:absolute;top:195px;left:0;width:1200px;height:472px;background:linear-gradient(90deg,#e2a27a 0%,#e9c36a 15%,#7aa275 27%,#557da8 35%,#dfe3e8 45%,#e6e8ea 100%)}
.hero-copy{position:absolute;left:600px;top:90px;width:500px;text-align:center}
.hero-copy h1{font-family:'Kaushan Script',cursive;font-weight:400;font-size:52px;line-height:1.25}
.hero-copy p{font-size:15.5px;line-height:1.6;margin:26px 0 30px}
.hero-scroll{position:absolute;left:1126px;top:60px;width:10px;height:362px;background:#d4d4d4}
.hero-scroll span{display:block;width:10px;height:55px;background:#999;margin-top:10px}
.hero-arrows{position:absolute;left:1112px;top:432px;display:flex}
.hero-arrows div{width:44px;height:38px;background:var(--white);border:1px solid var(--line);display:flex;align-items:center;justify-content:center}

/* section heads */
.sec-title{position:absolute;left:0;width:1200px;text-align:center;font-family:'Kaushan Script',cursive;font-size:56px;font-weight:400}
.sec-sub{position:absolute;left:0;width:1200px;text-align:center;font-size:17px}
.pager{position:absolute;left:0;width:1200px;display:flex;justify-content:center;gap:2px}

/* categories */
.cat-card{position:absolute;width:233px;height:242px;background:var(--white);box-shadow:0 2px 10px rgba(0,0,0,.12);display:flex;flex-direction:column;align-items:center;justify-content:center}
.cat-card h3{font-family:'Kaushan Script',cursive;font-weight:400;font-size:20px;margin-bottom:14px}
.tee{width:160px;height:180px}

/* products */
.band{position:absolute;left:0;width:1200px;background:var(--paper)}
.prod-card{position:absolute;top:1817px;width:233px;height:358px;background:var(--white);box-shadow:0 2px 8px rgba(0,0,0,.1)}
.prod-card .photo{height:228px}
.prod-card h3{font-family:'Kaushan Script',cursive;font-weight:400;font-size:20px;margin:18px 0 4px 30px}
.stars{margin-left:30px;color:var(--star);font-size:13px;letter-spacing:2px}
.price{margin:12px 0 0 30px;font-size:17px}

/* about */
.mission{position:absolute;left:645px;top:2575px;width:450px;text-align:center}
.mission h3{font-family:'Kaushan Script',cursive;font-weight:400;font-size:36px;margin:26px 0 20px}
.mission p{text-align:left;font-size:16.5px;line-height:1.75;margin-bottom:30px}
.dots{display:flex;justify-content:center;gap:12px;margin-top:22px}
.dots i{width:6px;height:6px;border-radius:50%;background:#bbb;display:block}
.dots i:first-child{background:var(--accent)}

/* team */
.team-card{position:absolute;top:3306px;width:313px;height:271px;background:var(--white);box-shadow:0 2px 10px rgba(0,0,0,.1);text-align:center;padding-top:26px}
.avatar{width:74px;height:74px;border-radius:50%;margin:0 auto;background:linear-gradient(#d9cbb9,#9c8a76)}
.team-card h3{font-family:'Kaushan Script',cursive;font-weight:400;font-size:21px;margin:14px 0 8px}
.team-card p{font-size:15.5px;line-height:1.55;padding:0 48px;text-align:justify;text-align-last:center}

/* blog */
.blog-card{position:absolute;top:3903px;width:475px;height:270px;background:var(--white);box-shadow:0 2px 10px rgba(0,0,0,.12);display:flex;padding:12px}
.blog-card .photo{width:176px;height:246px;flex:none}
.blog-body{padding:28px 0 0 22px}
.blog-body time{font-size:16px}
.blog-body h3{font-family:'Kaushan Script',cursive;font-weight:400;font-size:19px;margin:2px 0 18px}
.blog-body p{font-size:15px;line-height:1.6;margin-bottom:16px}

/* footer */
.site-footer{position:absolute;top:4285px;left:0;width:1200px;height:645px;background:var(--ink);color:var(--white)}
.f-col{position:absolute;top:92px}
.f-col h4{font-family:'Kaushan Script',cursive;font-weight:400;font-size:27px;line-height:1.15;margin-bottom:16px}
.f-col ul{list-style:none;font-size:15px;line-height:30px}
.f-col p{font-size:16.5px;line-height:1.8}
.socials{position:absolute;left:892px;top:368px;display:flex;gap:8px}
.socials span{width:34px;height:34px;background:var(--white);display:block}
.contact-title{position:absolute;top:440px;left:0;width:1200px;text-align:center;font-family:'Kaushan Script',cursive;font-size:25px}
.contact-form{position:absolute;top:500px;left:122px;width:954px;height:70px;border:1px solid var(--white);display:flex}
.contact-form span{flex:1;border-right:1px solid var(--white);padding:0 12px;display:flex;align-items:center;font-size:15px}
.send{width:190px;margin:4px;background:var(--white);color:var(--ink);display:flex;align-items:center;justify-content:center;font-weight:700;font-size:21px}
.apps{position:absolute;top:585px;left:0;width:1200px;display:flex;justify-content:center;gap:6px}
.apps span{border:1px solid var(--white);padding:6px 14px;font-size:12px;display:flex;align-items:center;gap:6px}
.copyright{position:absolute;top:4930px;left:0;width:1200px;height:70px;background:var(--ink);color:var(--white);font-size:12px;display:flex;align-items:center;justify-content:space-between;padding:0 60px 0 112px;border-top:1px solid #333}
</style>
</head>
<body>

<header class="site-header">
  <div class="logo">Bold Dawn</div>
  <nav class="main-nav"><span>Home</span><span>About us</span><span>Products</span><span>Team</span><span>Blog</span><span>Contact</span></nav>
  <div class="header-icons">
    <svg width="22" height="22" viewBox="0 0 24 24" fill="none" stroke="#000" stroke-width="1.8"><circle cx="12" cy="12" r="10"/><circle cx="12" cy="10" r="3.5"/><path d="M5.5 19c2-3 11-3 13 0"/></svg>
    <svg width="22" height="22" viewBox="0 0 24 24" fill="none" stroke="#000" stroke-width="1.8"><path d="M12 20s-8-5-8-11a4 4 0 0 1 8-1 4 4 0 0 1 8 1c0 6-8 11-8 11z"/></svg>
    <svg width="22" height="22" viewBox="0 0 24 24" fill="#000"><path d="M4 8h16l-1.5 13h-13z"/><path d="M8 8a4 4 0 0 1 8 0" fill="none" stroke="#000" stroke-width="1.8"/></svg>
  </div>
</header>

<div class="search-bar">
  <div class="search-field">Search
    <span class="search-btn"><svg width="16" height="16" viewBox="0 0 24 24" fill="none" stroke="#fff" stroke-width="3"><circle cx="10" cy="10" r="7"/><path d="M15 15l6 6"/></svg></span>
  </div>
  <div class="perk"><svg width="30" height="28" viewBox="0 0 24 24" fill="#fff"><rect x="3" y="9" width="18" height="4"/><rect x="4" y="13" width="16" height="8"/><rect x="11" y="9" width="2" height="12" fill="#000"/><path d="M12 9C9 4 5 6 8 9zM12 9c3-5 7-3 4 0z"/></svg><span>Gift<br>Certificates</span></div>
  <div class="perk"><svg width="28" height="28" viewBox="0 0 24 24" fill="none" stroke="#fff" stroke-width="2.6"><path d="M19 4L5 20"/><circle cx="6.5" cy="6.5" r="3"/><circle cx="17.5" cy="17.5" r="3"/></svg><span>Biggest<br>Sale</span></div>
</div>

<div class="promo">Use #FIRSTORDER And Get 50% Off On Your First Order Place !</div>

<section class="hero">
  <div role="img" aria-label="Row of colourful t-shirts on wooden hangers" style="position:absolute;inset:0"></div>
  <div class="hero-copy">
    <h1>Find Your New Collection On Discount !</h1>
    <p>Lorem ipsum dolor sit amet, consectetur adipiscing elit, sed do eiusmod tempor incididunt ut labore et dolore magna aliqua. Ut enim ad minim veniam, quis nostrud</p>
    <span class="btn">SHOP NOW</span>
  </div>
  <div class="hero-scroll"><span></span></div>
  <div class="hero-arrows">
    <div><svg width="10" height="14" viewBox="0 0 10 14" fill="none" stroke="#666" stroke-width="1.5"><path d="M8 1L2 7l6 6"/></svg></div>
    <div><svg width="10" height="14" viewBox="0 0 10 14" fill="none" stroke="#666" stroke-width="1.5"><path d="M2 1l6 6-6 6"/></svg></div>
  </div>
</section>

<h2 class="sec-title" style="top:760px">Shop Featured Categories</h2>
<p class="sec-sub" style="top:858px">Sed ut perspiciatis unde omnis iste natus</p>

<div class="cat-card" style="left:111px;top:951px"><div class="tee" role="img" aria-label="Navy blue t-shirt" style="background:linear-gradient(#2b3768,#1c2550);border-radius:40px 40px 6px 6px"></div></div>
<div class="cat-card" style="left:359px;top:951px"><h3>lorem ipsum dolor</h3><span class="btn">VIEW DETAILS</span></div>
<div class="cat-card" style="left:608px;top:951px"><div class="tee" role="img" aria-label="Grey t-shirt" style="background:linear-gradient(#b9b9b9,#9c9c9c);border-radius:40px 40px 6px 6px"></div></div>
<div class="cat-card" style="left:854px;top:951px"><h3>lorem ipsum dolor</h3><span class="btn">VIEW DETAILS</span></div>
<div class="cat-card" style="left:111px;top:1208px"><div class="tee" role="img" aria-label="Black printed t-shirt" style="background:linear-gradient(#2a2a2a,#111);border-radius:40px 40px 6px 6px"></div></div>
<div class="cat-card" style="left:359px;top:1208px"><h3>lorem ipsum dolor</h3><span class="btn">VIEW DETAILS</span></div>
<div class="cat-card" style="left:608px;top:1208px"><div class="tee" role="img" aria-label="Green t-shirt" style="background:linear-gradient(#3f8a5e,#2e6b48);border-radius:40px 40px 6px 6px"></div></div>
<div class="cat-card" style="left:854px;top:1208px"><h3>lorem ipsum dolor</h3><span class="btn">VIEW DETAILS</span></div>

<section class="band" style="top:1555px;height:753px"></section>
<h2 class="sec-title" style="top:1645px">Our Products</h2>
<p class="sec-sub" style="top:1743px">Sed ut perspiciatis unde omnis iste natus</p>

<div class="prod-card" style="left:111px"><div class="photo" role="img" aria-label="Model wearing a black t-shirt" style="background:linear-gradient(#e8e8e8,#2a2a2a 40%,#1a1a1a)"></div><h3>lorem ipsum dolor</h3><div class="stars">☆☆☆☆☆</div><div class="price">$ 00.00</div></div>
<div class="prod-card" style="left:359px"><div class="photo" role="img" aria-label="Model wearing a white printed t-shirt" style="background:linear-gradient(#d8d8d8,#f4f4f4 40%,#cfcfcf)"></div><h3>lorem ipsum dolor</h3><div class="stars">☆☆☆☆☆</div><div class="price">$ 00.00</div></div>
<div class="prod-card" style="left:608px"><div class="photo" role="img" aria-label="Model wearing a fitted black t-shirt" style="background:linear-gradient(#8f8f8f,#1b1b1b 35%,#262626)"></div><h3>lorem ipsum dolor</h3><div class="stars">☆☆☆☆☆</div><div class="price">$ 00.00</div></div>
<div class="prod-card" style="left:854px"><div class="photo" role="img" aria-label="Model wearing a red t-shirt" style="background:linear-gradient(#a9a9a9,#d61c1c 35%,#b81515)"></div><h3>lorem ipsum dolor</h3><div class="stars">☆☆☆☆☆</div><div class="price">$ 00.00</div></div>

<div class="pager" style="top:2238px">
  <svg width="28" height="24" viewBox="0 0 28 24" fill="none" stroke="#000" stroke-width="1.5"><circle cx="16" cy="12" r="10"/><path d="M22 12H2m4-4l-4 4 4 4"/></svg>
  <svg width="28" height="24" viewBox="0 0 28 24" fill="none" stroke="#000" stroke-width="1.5"><circle cx="12" cy="12" r="10"/><path d="M6 12h20m-4-4l4 4-4 4"/></svg>
</div>

<h2 class="sec-title" style="top:2405px">About Us</h2>
<p class="sec-sub" style="top:2493px">Sed ut perspiciatis unde omnis iste natus</p>
<div class="abs" role="img" aria-label="Shirts in white, yellow and orange hanging on a rail" style="left:111px;top:2557px;width:489px;height:501px;background:linear-gradient(90deg,#efe8dc 0%,#e9c46c 35%,#efe9dd 55%,#e7a238 80%,#d48a2a 100%)"></div>
<div class="mission">
  <div role="img" aria-label="White shirt with brand print" style="width:150px;height:170px;margin:0 auto;background:linear-gradient(#f5f5f5,#dcdcdc);border-radius:40px 40px 6px 6px"></div>
  <h3>Mission</h3>
  <p>Sed ut perspiciatis unde omnis iste natus error sit voluptatem accusantium doloremque laudantium, totam rem aperiam.</p>
  <span class="btn">READ MORE</span>
  <div class="dots"><i></i><i></i></div>
</div>
<div class="pager" style="top:3110px">
  <svg width="28" height="24" viewBox="0 0 28 24" fill="none" stroke="#000" stroke-width="1.5"><circle cx="16" cy="12" r="10"/><path d="M22 12H2m4-4l-4 4 4 4"/></svg>
  <svg width="28" height="24" viewBox="0 0 28 24" fill="none" stroke="#000" stroke-width="1.5"><circle cx="12" cy="12" r="10"/><path d="M6 12h20m-4-4l4 4-4 4"/></svg>
</div>

<section class="band" style="top:3195px;height:488px"></section>
<div class="team-card" style="left:111px"><div class="avatar" role="img" aria-label="Team member portrait"></div><h3>lorem ipsum dolor</h3><p>Sed ut perspiciatis unde omnis iste natus error sit voluptatem accusantium doloremque.</p></div>
<div class="team-card" style="left:442px"><div class="avatar" role="img" aria-label="Team member portrait"></div><h3>lorem ipsum dolor</h3><p>Sed ut perspiciatis unde omnis iste natus error sit voluptatem accusantium doloremque.</p></div>
<div class="team-card" style="left:773px"><div class="avatar" role="img" aria-label="Team member portrait"></div><h3>lorem ipsum dolor</h3><p>Sed ut perspiciatis unde omnis iste natus error sit voluptatem accusantium doloremque.</p></div>

<h2 class="sec-title" style="top:3740px">Blog</h2>
<p class="sec-sub" style="top:3824px">Sed ut perspiciatis unde omnis iste natus</p>
<article class="blog-card" style="left:111px">
  <div class="photo" role="img" aria-label="Colourful shirts on hangers" style="background:linear-gradient(90deg,#7a1f2e,#c23a4a 30%,#3a4f8a 60%,#8a6a9a)"></div>
  <div class="blog-body"><time>25 th Jun 2023</time><h3>lorem ipsum dolor</h3><p>Sed ut perspiciatis unde omnis iste natus error sit voluptatem accusantium doloremque</p><span class="btn">READ MORE</span></div>
</article>
<article class="blog-card" style="left:611px">
  <div class="photo" role="img" aria-label="Stack of bright folded t-shirts" style="background:linear-gradient(135deg,#2c8fd6,#e23a7a 30%,#f08a1c 55%,#f5d21e 80%,#f3f3f3)"></div>
  <div class="blog-body"><time>25 th July 2023</time><h3>lorem ipsum dolor</h3><p>Sed ut perspiciatis unde omnis iste natus error sit voluptatem accusantium doloremque</p><span class="btn">READ MORE</span></div>
</article>
<div class="pager" style="top:4220px">
  <svg width="28" height="24" viewBox="0 0 28 24" fill="none" stroke="#000" stroke-width="1.5"><circle cx="16" cy="12" r="10"/><path d="M22 12H2m4-4l-4 4 4 4"/></svg>
  <svg width="28" height="24" viewBox="0 0 28 24" fill="none" stroke="#000" stroke-width="1.5"><circle cx="12" cy="12" r="10"/><path d="M6 12h20m-4-4l4 4-4 4"/></svg>
</div>

<footer class="site-footer">
  <div class="f-col" style="left:112px;width:280px"><h4>About Us</h4><p>Sed ut perspiciatis unde omnis iste natus error sit voluptatem accusantium doloremque laudantium, totam rem aperiam.</p></div>
  <div class="f-col" style="left:411px"><h4>Navigate</h4><ul><li>About Us</li><li>Blog</li><li>Ask An Expert</li><li>Shipping &amp; Returns</li><li>Contact Us</li><li>Theme Features</li><li>Sitemap</li></ul></div>
  <div class="f-col" style="left:588px;top:72px"><h4>Popular<br>Brands</h4><ul><li>Fairweave</li><li>Northloom</li><li>Tidewell</li><li>View All</li></ul></div>
  <div class="f-col" style="left:741px"><h4>Categories</h4><ul><li>Food Items</li><li>Shop All</li><li>Electronics</li><li>Beauty Care</li><li>Fashion Style</li></ul></div>
  <div class="f-col" style="left:892px;width:220px"><h4>Location</h4><ul><li style="line-height:30px">482 Harbor Crest Road, Suite 7, Lakeview, Ohio, 44021</li><li>555 014 2398</li></ul></div>
  <div class="socials"><span></span><span></span><span></span><span></span></div>
  <div class="contact-title">CONTACT US</div>
  <div class="contact-form"><span>Name</span><span>Enter Email Address</span><div class="send">SEND</div></div>
  <div class="apps">
    <span><svg width="10" height="10" viewBox="0 0 10 10"><rect width="10" height="10" fill="#fff"/></svg>App Market</span>
    <span><svg width="10" height="10" viewBox="0 0 10 10"><path d="M1 0l9 5-9 5z" fill="#fff"/></svg>Play Market</span>
  </div>
</footer>
<div class="copyright"><span>© 2023 bolddawn - All Rights Reserved</span><span>C64</span></div>

</body>
</html>
```